Visitenkarten und Briefpapier
Zielgruppe
Planung und Realisierung von individuellen und wertbeständigen Kamin- und Ofenlösungen, sowie Fliesen- und Baddesign.
Aufgabenstellung
Wir benötigen ein möglichst schlichtes Design für Visitenkarten, bzw. Briefpapier. Für die Visitenkarten gerne auch Vorschläge mit Prägung, Ausstanzung oder mit Heißfolie. Auch Klappkarten wären denkbar. Das Design soll "das gewisse Etwas haben" und nicht zu verspielt sein.
Die Visitenkarten sind für die Firma KORVA, das Logo von der Ausstellung "raumfunke" soll dezent mit eingebunden werden (bei dem Briefpapier z.B. in der Fußzeile". Die farbliche Gestaltung sollte sich an den Farben des Logos orientieren.
Schriftart für Texte: Century Gothic
Schriftfarbe: RAL 7016
Nur eine Idee: Ich könnte mir auch gut vorstellen, dass die Visitenkarte aus einer Zündholzverpackung (wenn dann aber eine besondere mit nur einem Zündholz oder einem besonders breiten) besteht: http://glimmvelo.de/produkte_briefchen.php

```html
<!DOCTYPE html>
<html lang="de">
<head>
<meta charset="utf-8">
<title>KORVA – Visitenkarte</title>
<link rel="stylesheet" href="https://fonts.googleapis.com/css2?family=Questrial&display=swap">
<style>
  :root {
    --page-bg: #e4e4e2;
    --card-dark: #1d282c;
    --card-slate: #414c50;
    --card-light: #d0d1d1;
    --accent-orange: #c9780f;
    --ink-black: #111314;
    --text-light: #d9dbdc;
    --text-muted: #b9bdbf;
    --font-main: "Questrial", "Century Gothic", sans-serif;
  }
  * { box-sizing: border-box; margin: 0; padding: 0; }
  html, body {
    width: 1200px; height: 840px; overflow: hidden;
    background: var(--page-bg);
    font-family: var(--font-main);
  }
  .sheet {
    position: relative; width: 1200px; height: 840px;
    display: flex; align-items: center; justify-content: center; gap: 40px;
  }
  .card {
    position: relative; width: 540px; height: 350px;
    border-radius: 20px; overflow: hidden;
    box-shadow: 0 14px 30px rgba(0,0,0,.25);
  }
  .card-bg { position: absolute; inset: 0; width: 100%; height: 100%; }

  /* back side */
  .card--back { background: var(--card-dark); }
  .back-brand {
    position: absolute; inset: 0;
    display: flex; flex-direction: column; align-items: center; justify-content: center;
  }
  .back-brand .brand-name {
    font-size: 96px; letter-spacing: 6px; color: var(--text-light); line-height: 1;
  }
  .back-brand .brand-tagline {
    margin-top: 10px; font-size: 27px; letter-spacing: 2px; color: var(--text-light);
  }

  /* front side */
  .front-brand { position: absolute; left: 32px; top: 44px; }
  .front-brand .brand-name {
    font-size: 54px; letter-spacing: 3px; color: var(--ink-black); line-height: 1;
  }
  .front-brand .brand-tagline {
    margin-top: 6px; font-size: 17px; letter-spacing: 0.5px; color: var(--card-slate);
  }
  .person { position: absolute; right: 34px; top: 56px; text-align: right; }
  .person-name { font-size: 25px; letter-spacing: 1px; color: var(--accent-orange); line-height: 1.15; }
  .person-role { font-size: 16px; letter-spacing: 1px; color: var(--text-muted); margin-top: 2px; }

  .contact-list { position: absolute; right: 30px; top: 172px; list-style: none; }
  .contact-item {
    display: flex; align-items: center; justify-content: flex-end; gap: 12px;
    font-size: 18px; letter-spacing: 1.5px; color: var(--text-light); height: 29px;
  }
  .contact-icon { width: 22px; height: 18px; flex: none; }

  .address {
    position: absolute; left: 34px; bottom: 30px;
    display: flex; align-items: center; gap: 18px;
    font-size: 20px; letter-spacing: 1.5px; color: var(--text-light); line-height: 1.25;
  }
  .address-text { font-style: normal; }
  .address-pin { width: 22px; height: 30px; flex: none; }
</style>
</head>
<body>
<main class="sheet">

  <section class="card card--back" aria-label="Visitenkarte Rückseite">
    <div class="back-brand">
      <span class="brand-name">KORVA</span>
      <span class="brand-tagline">kamine · öfen · fliesen</span>
    </div>
  </section>

  <section class="card card--front" aria-label="Visitenkarte Vorderseite">
    <svg class="card-bg" viewBox="0 0 540 350" preserveAspectRatio="none" aria-hidden="true">
      <defs>
        <radialGradient id="slateGlow" cx="0.3" cy="0.75" r="0.9">
          <stop offset="0" stop-color="#505b5f"/>
          <stop offset="1" stop-color="#1f2a2e"/>
        </radialGradient>
      </defs>
      <rect width="540" height="350" fill="url(#slateGlow)"/>
      <path d="M0 0 H300 C300 140 200 200 0 225 Z" fill="var(--card-light)"/>
      <path d="M300 0 C300 140 200 200 6 226" fill="none" stroke="var(--ink-black)" stroke-width="5"/>
      <path d="M310 0 C308 150 210 210 10 231" fill="none" stroke="var(--accent-orange)" stroke-width="3"/>
    </svg>

    <div class="front-brand">
      <div class="brand-name">KORVA</div>
      <div class="brand-tagline">kamine · öfen · fliesen</div>
    </div>

    <div class="person">
      <div class="person-name">Jonas Berwin</div>
      <div class="person-role">Geschäftsführer</div>
    </div>

    <ul class="contact-list">
      <li class="contact-item">04821 / 73 19 40
        <svg class="contact-icon" viewBox="0 0 22 18" aria-label="Telefon"><path d="M5 2 L8 2 L9 6 L7 7.5 C8 10 10 12 12.5 13 L14 11 L18 12 L18 15 C18 16 17 17 16 17 C9 16 4 11 3 4 C3 3 4 2 5 2 Z" fill="var(--text-light)"/></svg>
      </li>
      <li class="contact-item">04821 / 73 19 48
        <svg class="contact-icon" viewBox="0 0 22 18" aria-label="Fax"><rect x="6" y="1" width="10" height="5" fill="var(--text-light)"/><rect x="1" y="6" width="20" height="7" rx="1.5" fill="var(--text-light)"/><rect x="5" y="11" width="12" height="6" fill="var(--text-light)" stroke="#2a3438" stroke-width="1"/><line x1="7" y1="13.5" x2="15" y2="13.5" stroke="#2a3438"/></svg>
      </li>
      <li class="contact-item">info@korva-lindau.de
        <svg class="contact-icon" viewBox="0 0 22 18" aria-label="E-Mail"><rect x="1.5" y="2.5" width="19" height="13" fill="none" stroke="var(--text-light)" stroke-width="1.5"/><path d="M1.5 2.5 L11 10 L20.5 2.5" fill="none" stroke="var(--text-light)" stroke-width="1.5"/></svg>
      </li>
    </ul>

    <div class="address">
      <svg class="address-pin" viewBox="0 0 22 30" aria-label="Adresse"><path d="M11 1 C5.5 1 1 5.3 1 10.8 C1 18 11 29 11 29 C11 29 21 18 21 10.8 C21 5.3 16.5 1 11 1 Z M11 14.5 A4 4 0 1 1 11 6.5 A4 4 0 1 1 11 14.5 Z" fill="var(--text-light)" fill-rule="evenodd"/></svg>
      <address class="address-text">Am Lindenhang 12a<br>27384 Falkenried</address>
    </div>
  </section>

</main>
</body>
</html>
```